Ledgers On Track Business Card Design

We are a bookkeeping and accounting practice and are particularly passionate about Vantu as 'state of the art' accounting software. We offer a number of services which are listed on the back of the card. The logos for LOT have already been developed. There are also other logos of organisations we are involved with - Vantu (both certified advisor and silver partner), QAG, and filenow hub. Regarding colours, we would like to use the colours similar to our website, www.ledgersontrack.com, and these connect with the www.vantu.com.au website. The proposed layout as it is just does not look too great - it looks like an amateur has done it - which is true!

Industry/Entity Type

Accounting

Contact Information for Business Card

The details to appear on the card are found on the files uploaded. I have front and back rough layouts.

```html
<!DOCTYPE html>
<html lang="en">
<head>
<meta charset="utf-8">
<title>Ledgers On Track – Business Card</title>
<link rel="stylesheet" href="https://fonts.googleapis.com/css2?family=Bree+Serif&family=PT+Serif:wght@400;700&display=swap">
<style>
  :root {
    --brand-blue: #4a5a9c;
    --brand-green: #5aab3f;
    --ink-grey: #5f5f5f;
    --ink-dark: #2f2f2f;
    --rule-grey: #c9c9c9;
    --badge-cyan: #1bb3d8;
    --badge-teal: #0f8a9c;
    --badge-silver: #a4a4a4;
    --partner-orange: #e2873a;
    --card-white: #fdfdfc;
    --page-bg: #e9e6e1;
  }
  * { box-sizing: border-box; margin: 0; padding: 0; }
  html, body { width: 1200px; height: 1023px; overflow: hidden; }
  body {
    background: var(--page-bg);
    font-family: "PT Serif", Georgia, serif;
    color: var(--ink-dark);
    display: flex;
    flex-direction: column;
    align-items: center;
    justify-content: center;
    gap: 56px;
  }
  .card {
    position: relative;
    width: 720px;
    height: 412px;
    background: var(--card-white);
    box-shadow: 0 6px 18px rgba(0,0,0,.18);
    overflow: hidden;
  }

  /* brand name */
  .brand {
    position: absolute;
    display: flex;
    align-items: center;
    gap: 16px;
    font-family: "Bree Serif", Georgia, serif;
    color: var(--brand-blue);
    line-height: 1;
  }
  .brand__dot {
    width: 42px; height: 42px;
    border-radius: 50%;
    background: var(--brand-green);
    flex: none;
  }

  /* back: services */
  .card--back .brand { left: 52px; top: 30px; font-size: 52px; }
  .services {
    position: absolute;
    left: 52px; top: 112px;
    list-style: none;
  }
  .services li {
    display: flex;
    align-items: baseline;
    gap: 10px;
    height: 31px;
    font-size: 19px;
    color: var(--ink-dark);
  }
  .services .tick { width: 16px; height: 14px; flex: none; align-self: center; }
  .services .label {
    font-family: "Bree Serif", Georgia, serif;
    font-size: 23px;
    color: var(--brand-blue);
  }
  .card--back .rule {
    position: absolute;
    left: 40px; right: 40px; top: 336px;
    height: 1px; background: var(--rule-grey);
  }
  .partner-row {
    position: absolute;
    left: 40px; right: 40px; top: 346px; height: 54px;
    display: flex; align-items: center; justify-content: space-between;
  }

  /* partner marks */
  .partner {
    display: flex; align-items: center; gap: 8px;
    font-family: "PT Serif", Georgia, serif;
    font-size: 22px;
    color: var(--ink-grey);
  }
  .partner__dot {
    width: 30px; height: 30px; border-radius: 50%;
    background: var(--partner-orange);
  }
  .partner--filenow { font-size: 28px; font-weight: 700; color: var(--brand-blue); }
  .badges { display: flex; gap: 6px; }
  .badge { width: 54px; height: 54px; border-radius: 50%; }
  .badge--cyan { background: var(--badge-cyan); }
  .badge--teal { background: var(--badge-teal); }
  .badge--silver { background: var(--badge-silver); }

  /* front */
  .card--front .brand { left: 50px; top: 60px; font-size: 54px; }
  .person {
    position: absolute;
    left: 40px; top: 178px; width: 290px;
    text-align: center;
  }
  .person__name {
    font-family: "Bree Serif", Georgia, serif;
    font-size: 32px;
    color: var(--brand-blue);
    line-height: 1.1;
  }
  .person__credentials {
    margin-top: 6px;
    font-size: 17px;
    line-height: 1.3;
    color: var(--ink-grey);
  }
  .person .badges { justify-content: center; margin-top: 18px; }
  .person .badge { width: 72px; height: 72px; }
  .card--front .divider {
    position: absolute;
    left: 340px; top: 168px;
    width: 1px; height: 190px;
    background: var(--rule-grey);
  }
  .contacts {
    position: absolute;
    left: 400px; top: 180px;
    list-style: none;
    font-size: 17px;
    color: var(--ink-dark);
  }
  .contacts li { display: flex; align-items: center; gap: 12px; height: 23px; }
  .contacts .icon { width: 16px; height: 16px; flex: none; }
  .contacts .abn { padding-left: 6px; }
  .card--front .partner { position: absolute; left: 408px; top: 298px; font-size: 26px; }
  .address-band {
    position: absolute;
    left: 0; right: 0; bottom: 0; height: 54px;
    background: var(--brand-green);
    color: #fff;
    font-size: 17px;
    display: flex; align-items: center; justify-content: center;
  }
</style>
</head>
<body>

<svg width="0" height="0" style="position:absolute" aria-hidden="true">
  <defs>
    <symbol id="tick" viewBox="0 0 16 14">
      <path d="M1.5 7.5 L6 12 L14.5 2" fill="none" stroke="#5aab3f" stroke-width="3" stroke-linecap="round" stroke-linejoin="round"/>
    </symbol>
    <symbol id="icon-phone" viewBox="0 0 16 16">
      <rect width="16" height="16" rx="2" fill="#4a5a9c"/>
      <path d="M3.5 6.5 C3.5 4.5 12.5 4.5 12.5 6.5 L11 7.5 L9.8 6.4 L6.2 6.4 L5 7.5 Z M5 8.5 H11 V12 H5 Z" fill="#fff"/>
    </symbol>
    <symbol id="icon-mobile" viewBox="0 0 16 16">
      <rect width="16" height="16" rx="2" fill="#4a5a9c"/>
      <rect x="5" y="2.5" width="6" height="11" rx="1" fill="#fff"/>
      <rect x="6" y="4" width="4" height="7" fill="#4a5a9c"/>
    </symbol>
    <symbol id="icon-mail" viewBox="0 0 16 16">
      <rect width="16" height="16" rx="2" fill="#4a5a9c"/>
      <rect x="3" y="4.5" width="10" height="7" fill="#fff"/>
      <path d="M3 4.5 L8 8.5 L13 4.5" fill="none" stroke="#4a5a9c" stroke-width="1"/>
    </symbol>
    <symbol id="icon-web" viewBox="0 0 16 16">
      <rect width="16" height="16" rx="2" fill="#4a5a9c"/>
      <circle cx="8" cy="8" r="5" fill="none" stroke="#fff" stroke-width="1.2"/>
      <ellipse cx="8" cy="8" rx="2.2" ry="5" fill="none" stroke="#fff" stroke-width="1"/>
      <line x1="3" y1="8" x2="13" y2="8" stroke="#fff" stroke-width="1"/>
    </symbol>
  </defs>
</svg>

<!-- Back of card: services -->
<section class="card card--back" aria-label="Card back">
  <div class="brand"><span class="brand__dot"></span>Ledgers On Track</div>
  <ul class="services">
    <li><svg class="tick"><use href="#tick"/></svg><span><span class="label">Bookkeeping</span> - data entry, bank reconciliation and review</span></li>
    <li><svg class="tick"><use href="#tick"/></svg><span><span class="label">Payroll</span> - Vantu Payroll Specialist</span></li>
    <li><svg class="tick"><use href="#tick"/></svg><span><span class="label">BAS</span> - QAG Public BAS Practitioner</span></li>
    <li><svg class="tick"><use href="#tick"/></svg><span><span class="label">Training &amp; support</span> - Vantu Certified Advisor</span></li>
    <li><svg class="tick"><use href="#tick"/></svg><span><span class="label">Management reports</span></span></li>
    <li><svg class="tick"><use href="#tick"/></svg><span><span class="label">Tax</span> - filenow hub Member</span></li>
    <li><svg class="tick"><use href="#tick"/></svg><span><span class="label">HR services</span></span></li>
  </ul>
  <div class="rule"></div>
  <div class="partner-row">
    <div class="partner partner--qag"><span class="partner__dot"></span>QAG</div>
    <div class="badges">
      <span class="badge badge--cyan" role="img" aria-label="Vantu partner badge"></span>
      <span class="badge badge--silver" role="img" aria-label="Vantu silver partner badge"></span>
    </div>
    <div class="partner partner--filenow">filenow hub</div>
  </div>
</section>

<!-- Front of card: contact -->
<section class="card card--front" aria-label="Card front">
  <div class="brand"><span class="brand__dot"></span>Ledgers On Track</div>
  <div class="person">
    <p class="person__name">Nora Whitfield</p>
    <p class="person__credentials">B Comm MA PhD AQAG<br>Registered BAS agent</p>
    <div class="badges">
      <span class="badge badge--cyan" role="img" aria-label="Vantu badge"></span>
      <span class="badge badge--teal" role="img" aria-label="Vantu certified advisor badge"></span>
    </div>
  </div>
  <div class="divider"></div>
  <ul class="contacts">
    <li><svg class="icon"><use href="#icon-phone"/></svg>03 9555 0192</li>
    <li><svg class="icon"><use href="#icon-mobile"/></svg>0400 555 318</li>
    <li><svg class="icon"><use href="#icon-mail"/></svg>nora@ledgersontrack.com</li>
    <li><svg class="icon"><use href="#icon-web"/></svg>www.ledgersontrack.com</li>
    <li class="abn">ABN 51 824 603 117</li>
  </ul>
  <div class="partner partner--qag"><span class="partner__dot"></span>QAG</div>
  <div class="address-band">18 Harlow Crest Road, Greenvale VIC 3088</div>
</section>

</body>
</html>
```